Auction Company Wordpress Design Project

We need a WordPress design/concept for an established auctioneering company specializing in Benefit Auctions, Estate Auctions, Business Liquidations/Overstocks, and real estate marketing in the Chicago area. The winning design will have a professional look appealing to clients searching for these services.

Industry/Entity Type

Real Estate

Requirements
Must have
• - We will require winning designer to provide a layered PSD (Adobe photoshop) concept file, along with any non-standard font files used.

The site's navigation: 1) Home, 2) Auctions, 3) About Us, 4) Buyers, 5) Sellers, 6) Media, 7) Contact Us. Horizontal structure preferred.

A slideshow element will be represented (choice of files attached) preferably in the header. The following widgets will also be incorporated into sidebar (or other creative placement):
- Mailbright Loop email signup
- Featured Auctions (example shown in http://www.bidfromyardside.example/ as "Upcoming Auctions" widget)
- Vidstreamo video widget
- Social media widget for Pagenook, Chirpline, Vidstreamo icons
- Testimonials widget

Winning design will creatively use colors in logo (with perhaps accent color) with a professional, clean look. Client mentions liking the use of color in http://www.lotgleamer.example/

Footer of site will have generic contact info (phone number, email addresses, mailing address; a smaller instance of logo; and the attached association logos.
Nice to have
• - Use of drop-down menus should be demonstrated by incorporating mouse-over for 1) Upcoming, 2) Online, 3) Past, under the 'Auctions' main menu item (for clarity of design, this drop-down can be placed under any other menu item if necessary).
Should not have
• Please do not use auction gavels in the design.

```html
<!DOCTYPE html>
<html lang="en">
<head>
<meta charset="utf-8">
<title>Harborline Auction Realty</title>
<link href="https://fonts.googleapis.com/css2?family=Cabin:wght@400;500;600&family=Arimo:wght@400;700&display=swap" rel="stylesheet">
<style>
:root{
  --ink:#1c1f24;
  --dark:#2d333b;
  --darker:#15181c;
  --panel:#3a3f46;
  --gold:#a8893a;
  --beige:#e8e0c6;
  --beige-dark:#d6ccac;
  --paper:#f8f6f6;
  --line:#c9c9c9;
  --body:#5a5a5a;
  --white:#fff;
}
*{box-sizing:border-box;margin:0;padding:0}
html,body{width:960px;height:1200px;overflow:hidden}
body{position:relative;background:var(--paper);font-family:"Arimo",Arial,sans-serif;color:var(--ink)}
.abs{position:absolute}
.cabin{font-family:"Cabin",sans-serif}

.topbar{left:0;top:0;width:960px;height:10px;background:var(--dark)}
.header{left:0;top:10px;width:960px;height:127px;background:#fbfbfb}
.brand{left:120px;top:28px;display:flex;align-items:center;gap:8px}
.brand-square{width:30px;height:30px;background:var(--gold)}
.brand-name{font-family:"Cabin",sans-serif;font-weight:600;color:var(--dark);font-size:19px;line-height:22px}
.signup{left:616px;top:31px;font-size:10px;font-weight:700;color:var(--dark)}
.signup-input{left:716px;top:26px;width:156px;height:21px;border:1px solid #ccc;background:#fff;font-size:9.5px;color:#999;padding:4px 0 0 10px;text-align:center}
.join-btn{left:808px;top:55px;width:62px;height:21px;background:var(--darker);color:#fff;font-size:10px;font-weight:700;text-align:center;line-height:21px}
.follow{left:358px;top:98px;font-family:"Cabin",sans-serif;font-size:14.5px;color:var(--ink)}
.socials{left:446px;top:96px;display:flex;gap:8px}
.social{display:flex;align-items:center;gap:3px;font-family:"Cabin",sans-serif;font-size:10px;color:var(--dark)}
.social i{display:block;width:9px;height:9px;background:var(--gold)}
.phone-icon{left:703px;top:95px;width:21px;height:21px;background:var(--dark);border-radius:3px}
.phone{left:735px;top:96px;font-family:"Cabin",sans-serif;font-size:15px;color:#555;letter-spacing:.3px}

.nav{left:0;top:144px;width:960px;height:38px;background:linear-gradient(#f2ecd9,var(--beige-dark));border-top:1px solid #cfc5a4;border-bottom:1px solid #b9ae8d;display:flex}
.nav a{display:block;height:100%;line-height:37px;text-align:center;font-family:"Cabin",sans-serif;font-size:11.5px;color:var(--ink);text-decoration:none;border-right:1px solid #c7bd9c}
.nav a:last-child{border-right:none}

.hero{left:0;top:182px;width:960px;height:312px;background:var(--dark)}
.featured{left:89px;top:196px;width:223px;height:287px;background:linear-gradient(#454a51,#2a2e34);border:1px solid #51565d}
.featured h2{position:absolute;left:46px;top:14px;font-family:"Cabin",sans-serif;font-weight:400;font-size:16px;color:#f2f2f2}
.featured .house{position:absolute;left:6px;top:6px}
.featured .rule{position:absolute;left:0;top:40px;width:221px;height:2px;background:#23272c}
.featured h3{position:absolute;left:0;width:221px;top:62px;text-align:center;font-family:"Cabin",sans-serif;font-weight:400;font-size:12.5px;color:#fff}
.featured .thumb{position:absolute;left:41px;top:88px;width:141px;height:93px;border:2px solid #fff}
.featured p{position:absolute;left:6px;width:211px;top:199px;text-align:center;font-size:10px;line-height:14.5px;color:#fff}
.featured a{position:absolute;left:0;width:221px;top:242px;text-align:center;font-size:10px;color:#fff;text-decoration:underline}

.dropdown{left:307px;top:188px;width:141px}
.dropdown div{height:29px;line-height:29px;padding-left:29px;font-family:"Cabin",sans-serif;font-size:11px;color:#fff;background:#24282d;border-bottom:1px solid #3b4047}
.dropdown div.on{background:var(--beige);color:var(--ink)}

.slider{left:321px;top:196px;width:551px;height:288px;background:#fff;padding:4px}
.slide{width:100%;height:100%;background:linear-gradient(#7fb3e0 0%,#b6cfe3 35%,#e6dccb 55%,#8f8a78 80%,#4e5a3e 100%);position:relative}
.caption{position:absolute;left:0;bottom:0;width:100%;height:34px;background:linear-gradient(transparent,rgba(0,0,0,.55))}
.caption span{position:absolute;left:16px;top:6px;font-family:"Cabin",sans-serif;font-size:15px;color:#fff}
.dots{position:absolute;right:58px;top:12px;display:flex;gap:8px}
.dots i{display:block;width:9px;height:9px;border-radius:50%;background:#fff}
.dots i.on{background:var(--gold)}

.box{background:#fbfbfb;border:1px solid #eee}
.upcoming{left:80px;top:518px;width:233px;height:262px}
.box-title{position:absolute;left:13px;top:9px;font-family:"Cabin",sans-serif;font-size:16px;color:var(--ink)}
.box-title em{font-style:normal;color:var(--gold)}
.box-rule{position:absolute;left:13px;width:220px;height:2px;background:#cfcfcf}
.item-title{position:absolute;left:0;width:233px;text-align:center;font-family:"Cabin",sans-serif;font-size:10px;color:var(--gold)}
.item-thumb{position:absolute;width:74px;height:49px;border:1px solid #aaa}
.item-text{position:absolute;left:8px;width:219px;text-align:center;font-size:10px;line-height:14.5px;color:var(--ink)}

.welcome{left:324px;top:516px;font-family:"Cabin",sans-serif;font-size:14px;color:var(--ink)}
.welcome em{font-style:normal;color:var(--gold)}
.welcome-rule{left:324px;top:547px;width:544px;height:2px;background:#ccc}
.intro{left:329px;top:562px;width:280px;font-size:9.8px;line-height:14.4px;color:var(--body)}
.video{left:624px;top:563px;width:253px;height:164px;background:#111;padding:5px}
.video-frame{width:100%;height:137px;background:linear-gradient(110deg,#6a8a4a,#b7a48a 40%,#3b3c44 75%,#222);position:relative}
.play{position:absolute;left:103px;top:48px;width:42px;height:42px;border-radius:50%;background:rgba(40,40,40,.6)}
.controls{height:14px;margin-top:2px;background:linear-gradient(#eee,#bbb);position:relative}
.controls .bar{position:absolute;left:14px;top:6px;width:140px;height:3px;background:#888}
.controls .prog{position:absolute;left:14px;top:6px;width:50px;height:3px;background:#c44}

.testimonials{left:80px;top:790px;width:233px;height:183px}
.t-photo{position:absolute;left:13px;width:56px;height:49px}
.t-name{position:absolute;left:78px;font-size:9.8px;color:var(--ink)}
.t-text{position:absolute;left:78px;width:140px;font-size:9.8px;line-height:14.5px;color:#666}
.t-text b{color:var(--ink);margin-left:6px;font-size:9px}

.card{top:790px;height:183px;background:#fbfbfb;border:1px solid #ddd}
.card-head{position:absolute;left:0;top:-5px;width:233px;height:27px;background:linear-gradient(#4c5259,#22262b);color:#fff;text-align:center;line-height:27px;font-family:"Cabin",sans-serif;font-size:14px}
.card-photo{position:absolute;top:36px;width:153px;height:87px}
.card-text{position:absolute;left:14px;top:134px;width:220px;font-size:9.8px;line-height:14.5px;color:#666}
.card-text b{color:var(--ink);font-size:9px;margin-left:20px}

.sep{left:0;top:990px;width:960px;height:1px;background:#e2e2e2}
.badges{left:0;top:1000px;width:960px;height:100px}

.footer{left:0;top:1102px;width:960px;height:98px;background:var(--darker)}
.f-links{left:115px;top:1122px;font-family:"Cabin",sans-serif;font-size:11px;color:#aaa;word-spacing:2px}
.f-links span{margin:0 7px;color:#777}
.copy{left:115px;top:1156px;font-family:"Cabin",sans-serif;font-size:9px;color:#999}
.contact{left:603px;top:1137px;font-family:"Cabin",sans-serif;font-size:9px;line-height:19px;color:#ddd}
.f-brand{left:773px;top:1108px;width:87px;height:85px;background:#000;border:1px solid #333;display:flex;align-items:center;justify-content:center;text-align:center;font-family:"Cabin",sans-serif;font-weight:600;font-size:11.5px;line-height:14px;color:#ddd}
</style>
</head>
<body>

<div class="abs topbar"></div>
<header class="abs header"></header>

<div class="abs brand">
  <div class="brand-square"></div>
  <div class="brand-name">HARBORLINE<br>AUCTION<br>REALTY</div>
</div>

<div class="abs signup">Join Our Email List</div>
<div class="abs signup-input">Enter your email address</div>
<div class="abs join-btn">Join Now</div>

<div class="abs follow">Follow us on</div>
<div class="abs socials">
  <span class="social"><i></i>Pagenook</span>
  <span class="social"><i></i>Circlewave</span>
  <span class="social"><i></i>Chirpline</span>
  <span class="social"><i></i>Vidstreamo</span>
</div>

<div class="abs phone-icon">
  <svg width="21" height="21" viewBox="0 0 21 21"><path d="M7 5c1 0 2 3 1.5 3.8L7.6 10c.8 1.8 1.7 2.7 3.4 3.4l1.2-.9c.8-.5 3.8.5 3.8 1.5 0 1.2-1.4 2.5-2.6 2.5C9 16.5 4.5 12 4.5 7.6 4.5 6.4 5.8 5 7 5z" fill="#fff"/></svg>
</div>
<div class="abs phone">+1 (555) 014 27 80</div>

<nav class="abs nav">
  <a style="width:174px">Home</a>
  <a style="width:109px">Aboutus</a>
  <a style="width:129px">Auctions</a>
  <a style="width:113px">Buyers</a>
  <a style="width:129px">Sellers</a>
  <a style="width:119px">Media</a>
  <a style="width:187px">Contact Us.</a>
</nav>

<section class="abs hero"></section>

<aside class="abs featured">
  <svg class="house" width="36" height="34" viewBox="0 0 36 34"><path d="M3 17 18 4l15 13" fill="none" stroke="#c0392b" stroke-width="3"/><rect x="8" y="16" width="20" height="17" fill="#f1e3c4"/><rect x="15" y="22" width="6" height="11" fill="#8a5a2b"/></svg>
  <h2>Featured Auctions</h2>
  <div class="rule"></div>
  <h3>Single Family Home Auction</h3>
  <div class="thumb" role="img" aria-label="Photo of a modern family home at dusk" style="background:linear-gradient(#b9c7d3,#6e6a5e 60%,#3f6f8a)"></div>
  <p>Original Price: $6.1M - Sealed Bid Auction, Jan. 7th - Published Reserve $3.8 M</p>
  <a>Click here for detail</a>
</aside>

<div class="abs slider">
  <div class="slide" role="img" aria-label="Photo of a suburban house at dusk with an auction sign on the lawn">
    <div class="caption"><span>Lorem ipsum dolor sit amet,</span>
      <div class="dots"><i></i><i class="on"></i><i></i><i></i><i></i></div>
    </div>
  </div>
</div>

<div class="abs dropdown">
  <div class="on">Upcoming</div>
  <div>Online</div>
  <div>Past</div>
</div>

<aside class="abs box upcoming">
  <div class="box-title">Upcomming <em>&nbsp;Auctions</em></div>
  <div class="box-rule" style="top:30px"></div>
  <div class="item-title" style="top:40px">Single Family Home Auction</div>
  <div class="item-thumb" role="img" aria-label="Photo of a modern family home" style="left:74px;top:58px;background:linear-gradient(#b9c7d3,#6e6a5e 60%,#3f6f8a)"></div>
  <div class="item-text" style="top:112px">Original Price: $6.1M - Sealed Bid Auction, Jan. 7th - Published Reserve $3.8 M</div>
  <div class="item-title" style="top:151px">Single Family Home Auction</div>
  <div class="item-thumb" role="img" aria-label="Photo of a modern family home" style="left:79px;top:170px;background:linear-gradient(#b9c7d3,#6e6a5e 60%,#3f6f8a)"></div>
  <div class="item-text" style="top:227px">Original Price: $6.1M - Sealed Bid Auction, Jan. 7th - Published Reserve $3.8 M</div>
</aside>

<h1 class="abs welcome" style="font-weight:400">WELCOME TO <em>HARBORLINE AUCTION REALTY</em></h1>
<div class="abs welcome-rule"></div>
<p class="abs intro">We would like to say a big Thankyou.We would like to say a big Thankyou.We would like to say a big Thankyou.We would like to say a big Thankyou.We would like to say a big Thankyou.We would like to say a big Thankyou.We would like to say a big Thankyou.We would like to say a big Thankyou.We would like to say a big Thankyou.We would like to say a big Thankyou.We would like to say a big Thankyou.We would like to say a big Thankyou.We would like to say a big Thankyou.We would like to say a big Thankyou.We would like to say a big Thankyou.We would like to say a big Thankyou.We</p>

<div class="abs video">
  <div class="video-frame" role="img" aria-label="Video still of an agent reviewing papers with a couple">
    <div class="play"><svg width="42" height="42" viewBox="0 0 42 42"><path d="M16 12l14 9-14 9z" fill="#ddd"/></svg></div>
  </div>
  <div class="controls"><div class="bar"></div><div class="prog"></div></div>
</div>

<aside class="abs box testimonials">
  <div class="box-title" style="left:12px;top:2px">Clinets <em>Testimonials</em></div>
  <div class="box-rule" style="top:24px;left:12px"></div>
  <div class="t-photo" role="img" aria-label="Photo of a client in front of a house" style="top:38px;background:linear-gradient(#9fb8cf,#4c4c52)"></div>
  <div class="t-name" style="top:37px">Mr &amp; Mrs&nbsp; Harlan Brooke WA</div>
  <div class="t-text" style="top:55px">We would like to say a big Thankyou.<br>The renovations ....<b>Read more</b></div>
  <div class="t-photo" role="img" aria-label="Photo of a client in front of a house" style="top:112px;background:linear-gradient(#9fb8cf,#4c4c52)"></div>
  <div class="t-name" style="top:112px">Mr &amp; Mrs&nbsp; Harlan Brooke WA</div>
  <div class="t-text" style="top:129px">We would like to say a big Thankyou.<br>The renovations ....<b>Read more</b></div>
</aside>

<section class="abs card" style="left:325px;width:267px">
  <div class="card-head">Buyers</div>
  <div class="card-photo" role="img" aria-label="Photo of bidders raising numbered paddles" style="left:45px;background:linear-gradient(135deg,#c8a36a,#8a4b2e 55%,#3a2a22)"></div>
  <p class="card-text">We would like to say a big Thankyou.We would like to say a big Thankyou.We would like to say a big Thankyou.<b>Read more....</b></p>
</section>

<section class="abs card" style="left:595px;width:261px">
  <div class="card-head" style="left:0">Sellers</div>
  <div class="card-photo" role="img" aria-label="Photo of bidders raising numbered paddles" style="left:46px;background:linear-gradient(135deg,#c8a36a,#8a4b2e 55%,#3a2a22)"></div>
  <p class="card-text" style="left:15px">We would like to say a big Thankyou.We would like to say a big Thankyou.We would like to say a big Thankyou.<b>Read more....</b></p>
</section>

<div class="abs sep"></div>

<svg class="abs badges" viewBox="0 0 960 100" aria-label="Association membership badges" role="img">
  <g fill="#555">
    <rect x="106" y="20" width="46" height="64" rx="4"/><rect x="180" y="20" width="42" height="62" rx="4"/><rect x="253" y="20" width="44" height="58" rx="4"/>
    <rect x="360" y="20" width="46" height="64" rx="4"/><rect x="434" y="20" width="42" height="62" rx="4"/><rect x="507" y="20" width="44" height="58" rx="4"/>
    <rect x="615" y="20" width="46" height="64" rx="4"/><rect x="688" y="20" width="42" height="62" rx="4"/><rect x="761" y="20" width="44" height="58" rx="4"/>
  </g>
</svg>

<footer class="abs footer"></footer>
<div class="abs f-links">Home <span>\</span>Auctions<span>\</span>About Us<span>\</span>Buyers<span>\</span>Sellers<span>\</span>Media<span>\</span>Contact Us.</div>
<div class="abs copy">Copyright © 2007 - 2013 - HARBORLINEAUCTIONS.EXAMPLE. - All Rights Reserved.</div>
<div class="abs contact">TOLL-FREE: (555) 019-4432<br>EMAIL: HARBORLINEAUCTIONS.EXAMPLE</div>
<div class="abs f-brand">HARBORLINE<br>AUCTION<br>REALTY</div>

</body>
</html>
```